body therapist

I need to offer my services as a massage therapist at home, acclimating customer space aroma candles with music and everything else to bring comfort. 8 offer rituals like this: relaxing ritual, purifying ritual, ritual breast, facial and body cleansing ritual organic, ritual man, ritual feet, slimming ritual. Naraja handling colors, seawater, green, lavender

Target Market(s)

men and women, tired, stressed, looking for something new

Font styles to use
Decorative
Script

Colors
f37122
0493ce
abd037

Requirements
Must have
• detailing each massage
Nice to have
• simple and elegant

```html
<!DOCTYPE html>
<html lang="es">
<head>
<meta charset="utf-8">
<title>Rituales Serenia</title>
<link rel="stylesheet" href="https://fonts.googleapis.com/css2?family=Special+Elite&family=Gochi+Hand&family=Roboto:wght@300&display=swap">
<style>
  :root {
    --backdrop: #dedede;
    --paper: #ffffff;
    --tab: #e6e6e6;
    --lime: #a9cf38;
    --orchid: #c65cc7;
    --panel-top: #dfe0e2;
    --panel-bottom: #fbfbfb;
    --ink: #555657;
    --white: #ffffff;
  }
  * { margin: 0; padding: 0; box-sizing: border-box; }
  html, body { width: 1000px; height: 1200px; overflow: hidden; background: var(--backdrop); }
  .page {
    position: absolute; left: 116px; top: 33px; width: 784px; height: 1113px;
    background: var(--paper); overflow: hidden;
  }
  .page-art { position: absolute; inset: 0; }
  .page-number {
    position: absolute; left: 347px; top: 0; width: 89px; height: 67px;
    background: var(--tab); border-radius: 0 0 44px 44px;
    font: 300 22px/1 'Roboto', sans-serif; color: #333;
    display: flex; align-items: center; justify-content: center;
  }
  .ritual-panel {
    position: absolute; left: 94px; top: 307px; width: 316px; height: 736px;
    background: linear-gradient(180deg, var(--panel-top) 0%, var(--panel-bottom) 100%);
    border: 1px solid #cfd2d6;
    padding: 18px 0 0 30px;
  }
  .ritual-title {
    font: 400 46px/46px 'Special Elite', monospace; color: var(--orchid);
    letter-spacing: 1px;
  }
  .ritual-list { list-style: none; margin-top: 34px; }
  .ritual-list li {
    position: relative; padding-left: 26px; padding-right: 10px;
    font: 400 21px/33px 'Gochi Hand', cursive; color: var(--ink);
    letter-spacing: 0.5px; font-style: italic;
  }
  .ritual-list li::before {
    content: ""; position: absolute; left: 0; top: 11px; width: 12px; height: 12px;
    background: var(--orchid);
  }
  .ritual-note {
    margin: 30px 10px 0 26px;
    font: 400 21px/30px 'Gochi Hand', cursive; color: var(--ink); font-style: italic;
    letter-spacing: 0.5px;
  }
  .duration-tag {
    position: absolute; left: 0; top: 932px; width: 257px; height: 77px;
    background: var(--lime); color: var(--white);
    font: 300 22px/30px 'Roboto', sans-serif; padding: 9px 0 0 36px;
  }
</style>
</head>
<body>
  <div class="page">
    <svg class="page-art" width="784" height="1113" viewBox="0 0 784 1113">
      <defs>
        <linearGradient id="orchidTones" x1="0" y1="0" x2="0" y2="1">
          <stop offset="0" stop-color="#ffffff"/>
          <stop offset="0.5" stop-color="#e7d6ec"/>
          <stop offset="1" stop-color="#eef0ee"/>
        </linearGradient>
        <linearGradient id="candleTones" x1="0" y1="0" x2="1" y2="1">
          <stop offset="0" stop-color="#d9b59a"/>
          <stop offset="0.45" stop-color="#d88a7a"/>
          <stop offset="0.75" stop-color="#e9ddd0"/>
          <stop offset="1" stop-color="#b4627a"/>
        </linearGradient>
      </defs>
      <rect class="orchid-photo" role="img" aria-label="Orquídeas lilas sobre tallos de bambú" x="0" y="40" width="784" height="350" fill="url(#orchidTones)"/>
      <rect class="lime-band" x="37" y="365" width="727" height="530" fill="var(--lime)"/>
      <path class="candle-photo" role="img" aria-label="Velas encendidas y flor roja en ambiente cálido"
            d="M0,1113 L0,930 C120,700 360,470 784,457 L784,1113 Z" fill="url(#candleTones)"/>
    </svg>
    <div class="page-number">4</div>
    <div class="ritual-panel">
      <h1 class="ritual-title">RITUALES<br>SERENIA</h1>
      <ul class="ritual-list">
        <li>RITUAL PURIFICANTE</li>
        <li>RITUAL VINOTERAPIA</li>
        <li>RITUAL MAMA</li>
        <li>RITUAL WELLNESS PIES</li>
        <li>RITUAL DE VITALIDAD PARA EL</li>
        <li>RITUAL PAREJA SERENIA SPA</li>
      </ul>
      <p class="ritual-note">TODOS NUESTROS RITUALES INCLUYEN MASAJE FACIAL CON AROMATERAPIA AMBIENTACION CON VELAS, AROMAS Y MUSICOTERAPIA</p>
    </div>
    <div class="duration-tag">ENTRE UNA Y DOS<br>HORAS APROX</div>
  </div>
</body>
</html>
```